my website is tavorinque.com. (brand name is ta belle vitrine) This is just a template that i have choose for. The content and the pictures are not about my business just the template.
I would like to have 4 pages for now. 1 homepage, which will be an overview for all pages, it is right now in this way. It will directly highlight my story. My website will tell an exclusive story about details which makes the difference and will make people happy with very small things. It will be art related but very stylish as well. I also want to have a event agenda on my homepage where people can see where my next event is. Page 2 my blog, where I will write weekly about mindset, lifestyle and details. Inspiration place for people who are looking for unique and exclusive approaches in life. Page 3 shop, where I will sell my stuff which is handmade and unique, it will be limited edition stuff. Mostly I will make the designs from marbling art, which I am a teacher for. (https://www.vidoranta.com/watch?v=KpwuzRaxTmo) check this video out for more. Page 4 is book page. Here people will be able to book private or group classes for marbling art (check the video). I have already a community of more than 500 people on gath rix, which will be my public as well. I wanna implement the gath rix button on this page as well. to be able to track.

This is about my website. I also need a logo for my brand, which will suit my website and my goals.

I can also give you a reference website, which really like as structure and style;
https://www.brightorvalco.com/products/the-morning-ledger?gclid=Xr4TpLmwq2HsVD9KEBsZTrc-WkPhyQ-uvlEjdRs3NKaOYFCBWMpuTzG8xyCVbhdnLWRqoaNf_2e8ZtpRvHbAwq9FLQ_hqgQ

Logo Text

ta belle vitrine

Coding

Coded - Design and coding required

Number of Pages Required

4 page

Requirements
Must have
• I can also give you a reference website, which really like as structure and style;
• https://www.brightorvalco.com/products/the-morning-ledger?gclid=Xr4TpLmwq2HsVD9KEBsZTrc-WkPhyQ-uvlEjdRs3NKaOYFCBWMpuTzG8xyCVbhdnLWRqoaNf_2e8ZtpRvHbAwq9FLQ_hqgQ

```html
<!DOCTYPE html>
<html lang="en">
<head>
<meta charset="utf-8">
<title>Ta Belle Vitrine</title>
<link href="https://fonts.googleapis.com/css2?family=Dancing+Script:wght@700&family=Open+Sans:wght@400;600;700&display=swap" rel="stylesheet">
<style>
:root{
  --ink:#222;
  --text:#555;
  --muted:#777;
  --red:#d0021b;
  --line:#dcdcdc;
  --white:#fff;
  --footer:#262626;
  --dark:#1b1b1b;
  --fb:#3b5998;
  --ig:#c13584;
}
*{margin:0;padding:0;box-sizing:border-box}
html,body{width:1200px;height:3529px;overflow:hidden;background:var(--white)}
body{position:relative;font-family:"Open Sans",Arial,sans-serif;color:var(--text)}
.abs{position:absolute}
.script{font-family:"Dancing Script",cursive;color:var(--ink);font-weight:700}
.topline{left:0;top:0;width:1200px;height:5px;background:var(--dark)}
.brand{left:99px;top:20px;display:flex;align-items:center;gap:14px}
.brand-dot{width:40px;height:40px;border-radius:50%;background:var(--ink)}
.brand-name{font-family:"Dancing Script",cursive;font-weight:700;font-size:27px;color:var(--ink);line-height:1}
.nav{left:640px;top:28px;display:flex;gap:36px;font-family:"Dancing Script",cursive;font-size:21px;font-weight:700;color:var(--ink)}
.nav-icons{left:982px;top:25px;display:flex;gap:10px;align-items:center}
.social{width:32px;height:32px;border-radius:50%}
.s1{background:var(--fb)}.s2{background:var(--ig)}

.hero{left:0;top:85px;width:1200px;height:562px;
  background:
    radial-gradient(ellipse 46% 40% at 54% 48%,#141414 0%,#1c1c1c 60%,rgba(28,28,28,0) 100%),
    linear-gradient(170deg,#8e8c88 0%,#4a4744 22%,#262626 45%,#2b2a28 70%,#77736d 100%)}
.hero-title{left:0;top:292px;width:1200px;text-align:center;font-size:86px;color:var(--white);line-height:1}
.hero-text{left:0;top:414px;width:1200px;text-align:center;font-size:15px;font-weight:600;line-height:34px;color:var(--white)}
.hero-btn{left:520px;top:517px;width:160px;height:47px;border:2px solid var(--white);color:var(--white);font-size:14px;font-weight:700;display:flex;align-items:center;justify-content:center;gap:8px}
.arrow{top:321px}

.story-title{left:97px;top:730px;font-size:44px;line-height:1.1}
.story-text{left:99px;top:812px;width:458px;font-size:13px;line-height:28px}
.story-text p{margin-bottom:16px}
.btn{border:2px solid var(--ink);color:var(--ink);font-size:13px;font-weight:700;display:flex;align-items:center;justify-content:center;gap:8px}
.story-btn{left:99px;top:1003px;width:138px;height:44px}
.video{left:612px;top:741px;width:487px;height:306px;
  background:radial-gradient(ellipse at 40% 35%,#c79a9b 0%,#9a6468 40%,#6b3f43 80%,#52302f 100%)}
.play{left:217px;top:127px}

.divider{left:99px;width:1002px;height:1px;background:var(--line)}
.sec-title{left:0;width:1200px;text-align:center;font-size:44px;line-height:1.1}
.sec-sub{left:0;width:1200px;text-align:center;font-size:12px;color:var(--muted)}

.product{width:236px}
.product .img{width:236px;height:226px;position:relative}
.product .name{margin-top:22px;text-align:center;font-size:16px;font-weight:600;color:var(--ink)}
.product .price{margin-top:6px;text-align:center;font-size:15px;color:var(--red)}
.cart-btn{margin:10px auto 0;width:128px;height:30px;border:1.5px solid var(--ink);display:flex;align-items:center;font-size:13px;color:var(--ink)}
.cart-btn .ic{width:30px;height:100%;background:var(--ink);display:flex;align-items:center;justify-content:center}
.cart-btn span{flex:1;text-align:center}
.badge{left:14px;top:14px;width:50px;height:50px;border-radius:50%;background:var(--dark);color:var(--white);font-size:14px;font-weight:700;display:flex;align-items:center;justify-content:center}

.band{left:0;top:1772px;width:1200px;height:437px;
  background:
    radial-gradient(ellipse 30% 40% at 22% 40%,rgba(150,80,90,.55),rgba(150,80,90,0)),
    radial-gradient(ellipse 30% 40% at 78% 70%,rgba(140,70,85,.5),rgba(140,70,85,0)),
    radial-gradient(ellipse 40% 50% at 55% 30%,rgba(110,120,60,.45),rgba(110,120,60,0)),
    #262a1e}
.band-title{left:0;top:1836px;width:1200px;text-align:center;font-size:46px;color:var(--white);line-height:1}
.band-text{left:0;top:1905px;width:1200px;text-align:center;font-size:13px;line-height:28px;color:var(--white)}
.stat{top:1995px;width:200px;text-align:center;color:var(--white)}
.stat .num{margin-top:12px;font-size:30px;font-weight:700;line-height:1.2}
.stat .lbl{font-size:13px;font-weight:600}

.event{width:311px}
.event .img{width:311px;height:219px;position:relative}
.event .head{margin-top:23px;display:flex;gap:12px}
.date{width:60px;height:64px;background:var(--dark);color:var(--white);text-align:center;padding-top:6px;line-height:1}
.date b{font-size:26px}.date small{font-size:9px;font-weight:700}
.date div{font-size:9px;margin-top:6px}
.ev-title{font-size:19px;font-weight:600;color:var(--ink)}
.ev-meta{margin-top:8px;font-size:12px;color:var(--muted);display:flex;align-items:center;gap:6px}
.ev-text{margin-top:10px;font-size:12.5px;line-height:23px;color:var(--muted)}
.book-now{left:100px;top:94px;width:111px;height:35px;background:var(--dark);color:var(--white);font-size:14px;display:flex;align-items:center;justify-content:center}

.grams{left:99px;top:3054px;display:flex;gap:2px}
.grams div{width:199px;height:205px}
.dots{left:572px;top:3291px;display:flex;gap:8px}
.dots i{width:12px;height:12px;border-radius:50%;border:1.5px solid #888}
.dots i.on{background:#333;border-color:#333}

.footer{left:0;top:3395px;width:1200px;height:134px;background:var(--footer)}
.foot-links{left:99px;top:3432px;font-size:13px;color:var(--white);word-spacing:4px}
.foot-copy{left:99px;top:3470px;font-size:11.5px;color:var(--white)}
.follow{left:845px;top:3430px;font-size:40px;color:var(--white);line-height:1.2}
.foot-social{left:1008px;top:3442px;display:flex;gap:12px}
.foot-social .social{width:40px;height:40px}
</style>
</head>
<body>
<div class="abs topline"></div>
<div class="abs brand"><div class="brand-dot"></div><span class="brand-name">ta belle vitrine</span></div>
<nav class="abs nav"><span>Home</span><span>My Blog</span><span>Shop</span><span>Book</span></nav>
<div class="abs nav-icons">
  <svg width="30" height="28" viewBox="0 0 30 28"><path d="M1 4h5l4 14h15l3-10H8" fill="none" stroke="#222" stroke-width="2.5"/><circle cx="12" cy="23" r="2.5" fill="#222"/><circle cx="23" cy="23" r="2.5" fill="#222"/><circle cx="25" cy="5" r="5" fill="#d0021b"/></svg>
  <div class="social s1"></div><div class="social s2"></div>
</div>

<section class="abs hero" role="img" aria-label="Marbling tray with floating coloured ink shapes"></section>
<svg class="abs arrow" style="left:30px" width="20" height="30" viewBox="0 0 20 30"><path d="M14 6 5 15l9 9" fill="none" stroke="#fff" stroke-width="3"/></svg>
<svg class="abs arrow" style="left:1150px" width="20" height="30" viewBox="0 0 20 30"><path d="M6 6l9 9-9 9" fill="none" stroke="#fff" stroke-width="3"/></svg>
<h1 class="abs script hero-title">Ta Belle Vitrine</h1>
<p class="abs hero-text">We provide an unparalleled selection of the very best quality products, an easy and comfortable<br>shopping experience, expedited shipping offers, and exceptional customer service.</p>
<div class="abs hero-btn">SHOP NOW <svg width="14" height="14" viewBox="0 0 14 14"><circle cx="7" cy="7" r="6" fill="#fff"/><path d="M6 4l3 3-3 3" fill="none" stroke="#222" stroke-width="1.8"/></svg></div>

<h2 class="abs script story-title">My Story</h2>
<div class="abs story-text">
  <p>Various versions have evolved over the years, sometimes by accident, sometimes on purpose injected humour and the like.</p>
  <p>There are many variations of passages of Lorem Ipsum available, but the majority have suffered alteration in some form, by injected humour, or randomised words which don't look even slightly believable.</p>
</div>
<div class="abs btn story-btn">READ MORE <svg width="13" height="13" viewBox="0 0 14 14"><circle cx="7" cy="7" r="6" fill="#222"/><path d="M6 4l3 3-3 3" fill="none" stroke="#fff" stroke-width="1.8"/></svg></div>
<div class="abs video" role="img" aria-label="Video still of a marbling lesson with a needle drawing through ink">
  <svg class="abs play" width="52" height="52" viewBox="0 0 52 52"><circle cx="26" cy="26" r="26" fill="#e62117"/><path d="M20 16l16 10-16 10z" fill="#fff"/></svg>
</div>

<div class="abs divider" style="top:1141px"></div>

<h2 class="abs script sec-title" style="top:1212px">Our Products</h2>
<p class="abs sec-sub" style="top:1277px">Check out our collection of new arrivals, best-sellers, and clearance items today.</p>

<div class="abs product" style="left:99px;top:1334px">
  <div class="img" role="img" aria-label="Handmade marbled cards on display" style="background:linear-gradient(180deg,#c9b7a0 0%,#a5574a 45%,#6c3a3a 75%,#2a2424 100%)"></div>
  <div class="name">Product Name Here</div><div class="price">€85.00</div>
  <div class="cart-btn"><div class="ic"><svg width="16" height="14" viewBox="0 0 16 14"><path d="M0 1h3l2 8h8l2-6H4" fill="none" stroke="#fff" stroke-width="1.6"/><circle cx="6" cy="12" r="1.3" fill="#fff"/><circle cx="12" cy="12" r="1.3" fill="#fff"/></svg></div><span>Add To Cart</span></div>
</div>
<div class="abs product" style="left:353px;top:1334px">
  <div class="img" role="img" aria-label="Framed marbled triangle artwork" style="background:radial-gradient(ellipse 38% 46% at 50% 50%,#e3a27e 0%,#d9b89a 55%,#c9a26a 75%,#9c7a52 100%)"></div>
  <div class="name">Product Name Here</div><div class="price">€85.00</div>
  <div class="cart-btn"><div class="ic"><svg width="16" height="14" viewBox="0 0 16 14"><path d="M0 1h3l2 8h8l2-6H4" fill="none" stroke="#fff" stroke-width="1.6"/><circle cx="6" cy="12" r="1.3" fill="#fff"/><circle cx="12" cy="12" r="1.3" fill="#fff"/></svg></div><span>Add To Cart</span></div>
</div>
<div class="abs product" style="left:609px;top:1334px">
  <div class="img" role="img" aria-label="Decorated hanging lantern" style="background:radial-gradient(ellipse 40% 45% at 50% 48%,#6e5a3e 0%,#b9a27c 50%,#e9e7e3 100%)"><div class="abs badge">35%</div></div>
  <div class="name">Product Name Here</div><div class="price">€85.00</div>
  <div class="cart-btn"><div class="ic"><svg width="16" height="14" viewBox="0 0 16 14"><path d="M0 1h3l2 8h8l2-6H4" fill="none" stroke="#fff" stroke-width="1.6"/><circle cx="6" cy="12" r="1.3" fill="#fff"/><circle cx="12" cy="12" r="1.3" fill="#fff"/></svg></div><span>Add To Cart</span></div>
</div>
<div class="abs product" style="left:866px;top:1334px">
  <div class="img" role="img" aria-label="Marbled red tulips on white paper" style="background:radial-gradient(ellipse 40% 50% at 45% 55%,#5f8a4a 0%,#b4c49e 35%,#ece7e6 75%,#f3f1f0 100%)"></div>
  <div class="name">Product Name Here</div><div class="price">€85.00</div>
  <div class="cart-btn"><div class="ic"><svg width="16" height="14" viewBox="0 0 16 14"><path d="M0 1h3l2 8h8l2-6H4" fill="none" stroke="#fff" stroke-width="1.6"/><circle cx="6" cy="12" r="1.3" fill="#fff"/><circle cx="12" cy="12" r="1.3" fill="#fff"/></svg></div><span>Add To Cart</span></div>
</div>

<section class="abs band" role="img" aria-label="Dark floral marbling pattern background"></section>
<h2 class="abs script band-title">Why Choose Us</h2>
<p class="abs band-text">We provide an unparalleled selection of the very best quality products, an easy and comfortable<br>shopping experience and exceptional customer service.</p>
<div class="abs stat" style="left:110px">
  <svg width="62" height="62" viewBox="0 0 62 62"><rect x="4" y="28" width="12" height="30" fill="#fff"/><path d="M20 30l12-22c4 0 6 3 5 8l-2 10h18c4 0 6 3 5 6l-5 22c-1 3-3 4-6 4H20z" fill="#fff"/></svg>
  <div class="num">800</div><div class="lbl">Finished Projects</div>
</div>
<div class="abs stat" style="left:372px">
  <svg width="62" height="62" viewBox="0 0 62 62"><path d="M8 14h22l8 8v32H8z" fill="none" stroke="#fff" stroke-width="4"/><path d="M24 6h22l8 8v32H40" fill="none" stroke="#fff" stroke-width="4"/></svg>
  <div class="num">999</div><div class="lbl">New Designs</div>
</div>
<div class="abs stat" style="left:628px">
  <svg width="62" height="62" viewBox="0 0 62 62"><circle cx="31" cy="18" r="9" fill="#fff"/><circle cx="13" cy="24" r="7" fill="#fff"/><circle cx="49" cy="24" r="7" fill="#fff"/><path d="M17 56c0-14 6-22 14-22s14 8 14 22z" fill="#fff"/><path d="M1 52c0-10 5-17 12-17 3 0 5 1 7 3-3 4-4 9-4 14z" fill="#fff"/><path d="M61 52c0-10-5-17-12-17-3 0-5 1-7 3 3 4 4 9 4 14z" fill="#fff"/></svg>
  <div class="num">500</div><div class="lbl">Team Members</div>
</div>
<div class="abs stat" style="left:890px">
  <svg width="62" height="62" viewBox="0 0 62 62"><circle cx="31" cy="31" r="26" fill="none" stroke="#fff" stroke-width="4"/><path d="M19 32l8 8 16-17" fill="none" stroke="#fff" stroke-width="4"/></svg>
  <div class="num">1000</div><div class="lbl">Happy Clients</div>
</div>

<h2 class="abs script sec-title" style="top:2281px">Upcoming Events</h2>
<p class="abs sec-sub" style="top:2345px">Read The Latest Events Regarding Our Ta Belle Vitrine Marbling Arts.</p>

<div class="abs event" style="left:99px;top:2412px">
  <div class="img" role="img" aria-label="Hand drawing pattern into marbling ink" style="background:linear-gradient(160deg,#dcd9d6 0%,#a39a92 40%,#8a6a62 70%,#c79a96 100%)"></div>
  <div class="head"><div class="date"><b>5</b><small> OCT</small><div>3:00PM</div></div><div><div class="ev-title">Event Name Here</div><div class="ev-meta"><svg width="13" height="11" viewBox="0 0 13 11"><path d="M1 1h11v7H5l-3 2V8H1z" fill="#888"/></svg>214 Comments &nbsp;| <svg width="11" height="11" viewBox="0 0 11 11"><rect x="0" y="5" width="2.5" height="6" fill="#888"/><path d="M3.5 5 6 0c1.2 0 1.6.8 1.3 2L7 4h3c.7 0 1 .5 1 1l-1 5c-.1.6-.5 1-1 1H3.5z" fill="#888"/></svg>895 Likes</div></div></div>
  <p class="ev-text">Nam libero tempore, cum soluta nobis est eligendi optio cumque nihil impedit quo minus id quod maxime placeat facere possimus</p>
</div>
<div class="abs event" style="left:445px;top:2412px">
  <div class="img" role="img" aria-label="Marbled paper sheet on a workshop table" style="background:linear-gradient(180deg,#4a4038 0%,#6d5446 35%,#9a4c3c 65%,#5a3a30 100%)"><div class="abs book-now">Book Now</div></div>
  <div class="head"><div class="date"><b>5</b><small> OCT</small><div>3:00PM</div></div><div><div class="ev-title">Event Name Here</div><div class="ev-meta"><svg width="13" height="11" viewBox="0 0 13 11"><path d="M1 1h11v7H5l-3 2V8H1z" fill="#888"/></svg>214 Comments &nbsp;| <svg width="11" height="11" viewBox="0 0 11 11"><rect x="0" y="5" width="2.5" height="6" fill="#888"/><path d="M3.5 5 6 0c1.2 0 1.6.8 1.3 2L7 4h3c.7 0 1 .5 1 1l-1 5c-.1.6-.5 1-1 1H3.5z" fill="#888"/></svg>895 Likes</div></div></div>
  <p class="ev-text">Nam libero tempore, cum soluta nobis est eligendi optio cumque nihil impedit quo minus id quod maxime placeat facere possimus</p>
</div>
<div class="abs event" style="left:788px;top:2412px">
  <div class="img" role="img" aria-label="Brushes and colourful paint pots" style="background:linear-gradient(135deg,#7c8a44 0%,#c8b54a 40%,#d88a5a 65%,#b44a78 100%)"></div>
  <div class="head"><div class="date"><b>5</b><small> OCT</small><div>3:00PM</div></div><div><div class="ev-title">Event Name Here</div><div class="ev-meta"><svg width="13" height="11" viewBox="0 0 13 11"><path d="M1 1h11v7H5l-3 2V8H1z" fill="#888"/></svg>214 Comments &nbsp;| <svg width="11" height="11" viewBox="0 0 11 11"><rect x="0" y="5" width="2.5" height="6" fill="#888"/><path d="M3.5 5 6 0c1.2 0 1.6.8 1.3 2L7 4h3c.7 0 1 .5 1 1l-1 5c-.1.6-.5 1-1 1H3.5z" fill="#888"/></svg>895 Likes</div></div></div>
  <p class="ev-text">Nam libero tempore, cum soluta nobis est eligendi optio cumque nihil impedit quo minus id quod maxime placeat facere possimus</p>
</div>

<div class="abs divider" style="top:2882px"></div>

<h2 class="abs script sec-title" style="top:2954px">Our Greatest Grams</h2>
<div class="abs grams">
  <div role="img" aria-label="Marbling workshop in progress" style="background:linear-gradient(135deg,#6a4a2a,#c6a06a 50%,#5a3a2a)"></div>
  <div role="img" aria-label="Framed red marbled artwork" style="background:radial-gradient(ellipse 40% 48% at 50% 50%,#c24a4a 0%,#d98a7a 55%,#d8c8a8 80%,#e6e0d8 100%)"></div>
  <div role="img" aria-label="Market stall with marbled cards" style="background:linear-gradient(180deg,#d6ccc2,#6a4a44 50%,#e2d6cc)"></div>
  <div role="img" aria-label="Colourful decorated lanterns" style="background:radial-gradient(ellipse at 50% 50%,#c8a040 0%,#2e5a6a 55%,#7a2a2a 100%)"></div>
  <div role="img" aria-label="Hands creating marbled pattern" style="background:linear-gradient(135deg,#3a4a8a,#b04a6a 50%,#d9a070)"></div>
</div>
<div class="abs dots"><i></i><i class="on"></i><i></i></div>

<footer class="abs footer"></footer>
<div class="abs foot-links">Home &nbsp;&nbsp;| &nbsp;&nbsp;My Blog &nbsp;&nbsp;| &nbsp;&nbsp;Shop &nbsp;&nbsp;| &nbsp;&nbsp;Book</div>
<div class="abs foot-copy">Copyright © 2017 &nbsp;Ta Belle Vitrine - All Rights Reserved.</div>
<div class="abs script follow">Follow Us:</div>
<div class="abs foot-social"><div class="social s1"></div><div class="social s2"></div></div>
</body>
</html>
```